Systems and Technology Consultants - Website

Design & Build a website for a new company which operates in the Systems and Technology space for Transportation, Government and Commercial sectors.

Overall design should be minimalist in nature.
Should also have a feed that provides news and event updates on the main page.
Logo has already been awarded and should be incorporated into the site.

We like the overall layout, functionality and simplicity of the below sites. Submitted designs could be similar to or a combination of the aspects on these sites, or perhaps a whole different concept - we are open to new ideas.
Norvique.com
Teblo.it

Update 1 Dated 27 May 2014

All I am moving away from the Teblo.it website and would like it to be more aligned with Norvique.com not only in layout but in functionality. I will be extending the deadline of this design brief for two weeks to incorporate additional requirements and will add addtional funding to the project.

Apologies for not having more information available to provide but with so many submissions its getting confusing.

Thanks Derek

Please note that the brief has been updated and the deadline has been extended.

Important: We will need two language versions of the website, English and Arabic; the website is hosted on HostPelican

Hello All, Thank you for your submissions. We have narrowed it down to the final 6 designers and I just wanted to take a moment and provide a bit of feedback regarding the concepts that we like and the modifications we are looking for. First, let me mention some of the design functions we like. - At the top of the homepage we really like the "region" or "language" tab so that the website can be viewed in both English and Arabic. - We like the homepage to have clear color variation so that the different sections of the homepage are distinct. Additionally, we like the bottom portion of the homepage to be in red. We feel that draws attention to our contact information. Again, we would like the colors to integrate black, gray-scale, red, etc. - Having a search tab at the top of the home page, or integrated into the main image, so that the site is easy to navigate. - We especially like the main image to have the scrolling tabs at the bottom so it is easy to browse the services offered (Consultancy, Solutions Architecture, Masters Systems Integration, Independent Design Review). - In regards to the services offered tab we really like the idea that a few people presented that have the outside of our logo with an icon in the middle of consultancy, solutions, etc., etc. Secondly, as mentioned in our brief we really enjoy the design of norvique site. Specially, we enjoy the strong iconic images they use, the way the tabs at the top scroll easily, and contact us page that generates an email. Lastly, I've included some photos of the concept we have been working on. What we are trying to demonstrate is how our company offers a range of services that are essentially linked together. We provide individual services that when combined present the full service package. We would like this concept to be integrated into the over concept of our website. Please feel free to ask for clarification of any of the above points or contact us if you have any additional questions. We appreciate all of your hard work and are very excited to see the updated designs. Best, Marta Vennick Quelbrant Senior Program Manager marta.vennick@quelbrant-example.com

Industry/Entity Type

Government

Font styles to use
Serif
Sans Serif

Requirements
Must have
• Must work on/adapt to various/mobile devices (responsive)
Must be simple and straightforward
Colors should be in line/matching with logo
2 language versions: English and Arabic (no Thai)
Services should be the first group/row of items after/below the main image
Note: the website will be hosted by hostpelican
Nice to have
• Submit feedback form
What's New section
The banner at the bottom of the site should not be too large; we would like a narrow one more
It would be nice if the header/top banner (with Home, About, etc. tabs) could stay in place as you scroll down (like Norvique and Chatterloop)
We will likely only use one image with a Company slogan on the Home page rather than a carousel of images to rotate through
Should not have
• This is the existing website: http://www.quelbrant-example.org
We do not like the animation, the way the banner icons/titles bounce
Not simple enough, we don't like the functionality or how pages load so slowly
We do not like the logo centered - it should be at the left
The banner and its tabs should not be towards the right, we would like them to be centered, to go all the way across and to be below the logo

```html
<!DOCTYPE html>
<html lang="en">
<head>
<meta charset="utf-8">
<title>Quelbrant – Home</title>
<link href="https://fonts.googleapis.com/css2?family=Open+Sans:wght@400;600;700&family=Arimo:wght@400&display=swap" rel="stylesheet">
<style>
:root{
  --red:#e31e24;
  --red-dark:#c4161c;
  --ink:#333333;
  --grey:#777777;
  --light:#e6e6e6;
  --footer:#2d2d2d;
  --footer-deep:#262626;
  --white:#ffffff;
}
*{margin:0;padding:0;box-sizing:border-box}
html,body{width:1016px;height:1200px;overflow:hidden;background:var(--white)}
body{position:relative;font-family:"Open Sans",Arial,sans-serif;color:var(--ink)}
.abs{position:absolute}
.top-rule{left:0;top:0;width:1016px;height:3px;background:var(--red)}

.brand{left:120px;top:38px;display:flex;align-items:center;gap:6px}
.brand-mark{width:12px;height:12px;background:var(--red)}
.brand-name{font-size:15px;font-weight:700;letter-spacing:2px;color:var(--red)}

.search{left:651px;top:42px;width:245px;height:25px;display:flex;border:1px solid #dcdcdc;box-shadow:inset 0 1px 3px rgba(0,0,0,.12)}
.search-field{flex:1;font-size:10px;color:#555;padding:6px 7px}
.search-button{width:27px;background:var(--red-dark);display:flex;align-items:center;justify-content:center}

.main-nav{left:120px;top:107px;width:776px;height:36px;background:linear-gradient(#3a3a3a,#050505);border-bottom:3px solid var(--red);border-radius:3px 3px 0 0;display:flex;justify-content:space-between;align-items:center;padding:0 8px}
.main-nav a{color:var(--white);font-size:11.5px;font-weight:600;text-decoration:none}
.main-nav a.current{color:var(--red)}

.hero{left:120px;top:143px;width:776px;height:346px;overflow:hidden}
.hero-photo{position:absolute;inset:0;
  background:
    linear-gradient(180deg,rgba(255,255,255,0) 0%,rgba(255,255,255,0) 70%,rgba(240,240,238,.9) 82%,#e9e9e6 100%),
    radial-gradient(ellipse at 22% 55%,rgba(45,40,45,.75),rgba(45,40,45,0) 38%),
    radial-gradient(ellipse at 82% 60%,rgba(205,185,165,.9),rgba(205,185,165,0) 35%),
    radial-gradient(ellipse at 50% 30%,#e4e8e1,#b9c2b4 60%,#9aa596 100%)}
.hero-curve{position:absolute;left:0;top:0}
.hero-dots{position:absolute;left:356px;top:318px;display:flex;gap:5px}
.hero-dots span{width:12px;height:12px;border-radius:50%;background:var(--red);border:2px solid var(--white);box-shadow:0 0 0 1px #999}
.hero-dots span:first-child{background:#999}

.welcome-title{left:120px;top:513px;width:776px;text-align:center;font-size:14px;font-weight:600;color:var(--red)}
.welcome-text{left:120px;top:545px;width:776px;text-align:center;font-family:"Arimo",Arial,sans-serif;font-size:9.6px;line-height:17.5px;color:var(--ink)}

.pager{left:864px;top:613px;display:flex;gap:4px}
.pager span{width:13px;height:13px;border-radius:50%;background:#a5a5a5;display:flex;align-items:center;justify-content:center}

.feature{top:636px;width:240px;height:92px}
.feature-icon{position:absolute;left:0;top:4px;width:78px;height:78px;border-radius:50%;background:radial-gradient(circle at 40% 35%,#f0474c,#b50f14);border:4px solid #f3f3f3;box-shadow:0 1px 4px rgba(0,0,0,.35);display:flex;align-items:center;justify-content:center}
.feature-rule{position:absolute;left:86px;top:0;width:1px;height:92px;background:var(--light)}
.feature-title{position:absolute;left:94px;top:6px;font-size:13px;font-weight:600;color:var(--red)}
.feature-text{position:absolute;left:94px;top:30px;width:150px;font-size:9.6px;line-height:13.6px;color:var(--grey)}

.divider-shadow{left:120px;top:744px;width:776px;height:10px;background:radial-gradient(ellipse at 50% 0,rgba(0,0,0,.12),transparent 70%)}

.section-title{left:120px;top:776px;font-size:14px;font-weight:600;color:var(--red)}
.view-all{left:835px;top:773px;width:61px;height:19px;background:var(--red);border-radius:3px;color:var(--white);font-size:8px;font-weight:700;display:flex;align-items:center;justify-content:center;gap:4px}
.section-rule{left:120px;top:804px;width:776px;height:1px;background:var(--light)}

.service-card{top:820px;width:170px;height:144px;border:2px solid var(--white);box-shadow:0 0 3px rgba(0,0,0,.35)}
.service-photo{position:absolute;inset:0}
.service-caption{position:absolute;left:0;bottom:0;width:100%;height:34px;background:rgba(30,30,30,.72);display:flex;align-items:center;justify-content:space-between;padding:0 4px 0 10px}
.service-caption span{color:var(--white);font-size:11.5px;font-weight:600}
.service-go{width:30px;height:22px;background:var(--white);border-radius:3px;display:flex;align-items:center;justify-content:center}

.site-footer{left:0;top:998px;width:1016px;height:166px;background:var(--footer)}
.footer-links{top:1010px;list-style:none;font-family:Arial,sans-serif;font-size:9.6px;line-height:23.8px;color:var(--white)}
.footer-heading{font-size:12.5px;font-weight:400;color:var(--white)}
.field{width:167px;height:26px;background:var(--white);font-family:Arial,sans-serif;font-size:9.6px;color:#444;padding:7px 4px}
.sign-up{left:590px;top:1120px;width:74px;height:26px;background:var(--red);color:var(--white);font-size:12px;display:flex;align-items:center;justify-content:center}
.contact-lines{left:723px;top:1035px;font-size:9.8px;line-height:16px;color:#e8e8e8;letter-spacing:.2px}
.copyright{left:0;top:1164px;width:1016px;height:36px;background:var(--footer-deep);border-top:1px solid #3a3a3a;font-family:Arial,sans-serif;font-size:9.2px;color:var(--white);text-align:center;line-height:34px}
</style>
</head>
<body>
<div class="abs top-rule"></div>

<div class="abs brand"><span class="brand-mark"></span><span class="brand-name">QUELBRANT</span></div>

<div class="abs search">
  <div class="search-field">Search</div>
  <div class="search-button">
    <svg width="12" height="12" viewBox="0 0 12 12"><circle cx="4.5" cy="4.5" r="3" fill="none" stroke="#fff" stroke-width="1.6"/><line x1="6.8" y1="6.8" x2="10.5" y2="10.5" stroke="#fff" stroke-width="2"/></svg>
  </div>
</div>

<nav class="abs main-nav">
  <a class="current">HOME</a><a>BUSINESS UNITS</a><a>SERVICES</a><a>ABOUT US</a><a>LOCATIONS</a><a>CONTACT US</a>
</nav>

<div class="abs hero">
  <div class="hero-photo" role="img" aria-label="Photo of two businesswomen talking across an office desk with a laptop and lamp"></div>
  <svg class="hero-curve" width="776" height="346" viewBox="0 0 776 346">
    <path d="M0 314 Q388 372 776 314 L776 346 L0 346 Z" fill="#fff"/>
    <path d="M0 314 Q388 372 776 314" fill="none" stroke="#e31e24" stroke-width="3"/>
  </svg>
  <div class="hero-dots"><span></span><span></span><span></span><span></span></div>
</div>

<h1 class="abs welcome-title">WELCOME TO OUR COMPANY</h1>
<p class="abs welcome-text">Lorem ipsum dolor sit amet, consectetur adipisicing elit, sed do eiusmod tempor incididunt ut labore et dolore magna aliqua. Ut enim ad minim veniam, quis nostrud exercitation ullamco laboris nisi ut aliquip ex ea commodo consequat. Duis aute irure dolor in reprehenderit in voluptate velit esse cillum dolore eu fugiat nulla pariatur. Excepteur sint occaecat cupidatat non proident, sunt in culpa qui officia deserunt mollit anim id est laborum</p>

<div class="abs pager">
  <span><svg width="6" height="8" viewBox="0 0 6 8"><path d="M4.5 1 L1.5 4 L4.5 7" fill="none" stroke="#fff" stroke-width="1.5"/></svg></span>
  <span><svg width="6" height="8" viewBox="0 0 6 8"><path d="M1.5 1 L4.5 4 L1.5 7" fill="none" stroke="#fff" stroke-width="1.5"/></svg></span>
</div>

<div class="abs feature" style="left:120px">
  <div class="feature-icon" role="img" aria-label="Mobile phone icon">
    <svg width="40" height="44" viewBox="0 0 40 44"><g transform="rotate(-28 20 22)"><rect x="11" y="4" width="18" height="36" rx="3" fill="#f4f4f4" stroke="#222" stroke-width="1.5"/><rect x="13.5" y="9" width="13" height="24" fill="#2b2b2b"/><circle cx="20" cy="36.5" r="1.6" fill="#222"/></g></svg>
  </div>
  <div class="feature-rule"></div>
  <h3 class="feature-title">Lorem ipsum dolor</h3>
  <p class="feature-text">Sed ut perspiciatis unde omnis iste natus error sit voluptatem accusantium doloremque lau-dantium, totam rem aperiam,</p>
</div>
<div class="abs feature" style="left:386px">
  <div class="feature-icon" role="img" aria-label="Light bulb icon">
    <svg width="36" height="46" viewBox="0 0 36 46"><circle cx="18" cy="16" r="12" fill="#ffd54a" stroke="#f0a81c" stroke-width="1.5"/><rect x="13" y="27" width="10" height="10" rx="1" fill="#d9d9d9" stroke="#888" stroke-width="1"/><line x1="13" y1="31" x2="23" y2="31" stroke="#888"/><line x1="13" y1="34" x2="23" y2="34" stroke="#888"/><rect x="15.5" y="37" width="5" height="3" fill="#555"/></svg>
  </div>
  <div class="feature-rule"></div>
  <h3 class="feature-title">Lorem ipsum dolor</h3>
  <p class="feature-text">Sed ut perspiciatis unde omnis iste natus error sit voluptatem accusantium doloremque lau-dantium, totam rem aperiam,</p>
</div>
<div class="abs feature" style="left:650px">
  <div class="feature-icon" role="img" aria-label="Rising bar chart icon">
    <svg width="44" height="40" viewBox="0 0 44 40"><rect x="4" y="28" width="6" height="9" fill="#5fb3e8"/><rect x="12" y="23" width="6" height="14" fill="#4aa2de"/><rect x="20" y="18" width="6" height="19" fill="#3a8fd0"/><rect x="28" y="12" width="6" height="25" fill="#2a7cc0"/><path d="M4 24 L14 17 L22 19 L36 6" fill="none" stroke="#ffb020" stroke-width="2.5"/><path d="M31 5 L38 4 L37 11 Z" fill="#ffb020"/></svg>
  </div>
  <div class="feature-rule"></div>
  <h3 class="feature-title">Lorem ipsum dolor</h3>
  <p class="feature-text">Sed ut perspiciatis unde omnis iste natus error sit voluptatem accusantium doloremque lau-dantium, totam rem aperiam,</p>
</div>

<div class="abs divider-shadow"></div>

<h2 class="abs section-title">OUR SERVICES</h2>
<div class="abs view-all">VIEW ALL <svg width="5" height="6" viewBox="0 0 5 6"><path d="M0 0 L5 3 L0 6Z" fill="#fff"/></svg></div>
<div class="abs section-rule"></div>

<div class="abs service-card" style="left:120px">
  <div class="service-photo" role="img" aria-label="Blue circuit board technology image" style="background:linear-gradient(135deg,#0a2a6a,#1f6fd0 55%,#0b2b5c)"></div>
  <div class="service-caption"><span>LOREM IPSUM</span><span class="service-go"><svg width="22" height="10" viewBox="0 0 22 10"><path d="M1 1l4 4-4 4M8 1l4 4-4 4M15 1l4 4-4 4" fill="none" stroke="#222" stroke-width="1.6"/></svg></span></div>
</div>
<div class="abs service-card" style="left:322px">
  <div class="service-photo" role="img" aria-label="Light blue jigsaw puzzle globe image" style="background:linear-gradient(135deg,#e6f6fb,#9fd2ea 60%,#5aa4c8)"></div>
  <div class="service-caption"><span>LOREM IPSUM</span><span class="service-go"><svg width="22" height="10" viewBox="0 0 22 10"><path d="M1 1l4 4-4 4M8 1l4 4-4 4M15 1l4 4-4 4" fill="none" stroke="#222" stroke-width="1.6"/></svg></span></div>
</div>
<div class="abs service-card" style="left:524px">
  <div class="service-photo" role="img" aria-label="Dark blue digital rings technology image" style="background:radial-gradient(circle at 35% 50%,#1e7fbf,#0a2f55 50%,#05101f)"></div>
  <div class="service-caption"><span>LOREM IPSUM</span><span class="service-go"><svg width="22" height="10" viewBox="0 0 22 10"><path d="M1 1l4 4-4 4M8 1l4 4-4 4M15 1l4 4-4 4" fill="none" stroke="#222" stroke-width="1.6"/></svg></span></div>
</div>
<div class="abs service-card" style="left:726px">
  <div class="service-photo" role="img" aria-label="Blue and violet fibre optic strands image" style="background:linear-gradient(135deg,#1a1030,#5b4fa8 45%,#2a8fe0 75%,#0a1a3a)"></div>
  <div class="service-caption"><span>LOREM IPSUM</span><span class="service-go"><svg width="22" height="10" viewBox="0 0 22 10"><path d="M1 1l4 4-4 4M8 1l4 4-4 4M15 1l4 4-4 4" fill="none" stroke="#222" stroke-width="1.6"/></svg></span></div>
</div>

<footer>
  <div class="abs site-footer"></div>
  <ul class="abs footer-links" style="left:122px"><li>Home</li><li>About</li><li>News</li><li>Services</li><li>What We Do</li><li>Contact Us</li></ul>
  <ul class="abs footer-links" style="left:230px"><li>Grief &amp; Healing</li><li>Resources</li><li>Plan Now</li><li>Locations</li><li>Privacy Policy</li><li>Terms &amp; Conditions</li></ul>
  <ul class="abs footer-links" style="left:366px"><li>Resources</li><li>Plan Now</li><li>Locations</li><li>Privacy Policy</li><li>Terms &amp; Conditions</li></ul>

  <h4 class="abs footer-heading" style="left:499px;top:1012px">NEWSLETTER SIGN UP</h4>
  <div class="abs field" style="left:499px;top:1043px">Enter Name</div>
  <div class="abs field" style="left:498px;top:1081px">Enter Email Address</div>
  <div class="abs sign-up">SIGN UP</div>

  <h4 class="abs footer-heading" style="left:722px;top:1012px">CONTACT US</h4>
  <p class="abs contact-lines">address: 14 Velmora Lane,<br>Harrowgate District, Calden 40712<br>phone numbers: +(00)-555-014-2276<br>email: info@quelbrant-example.org</p>

  <div class="abs copyright">Copyright 2005-2013 www.quelbrant-example.biz All rights reserved.</div>
</footer>
</body>
</html>
```